Plakate für Charity Unternehmen
Zielgruppe
Orvu ist ein weltweit agierendes Charity Unternehmen.
Aufgabenstellung
Wir benötigen ein 'Plakat' Design, mit dem Zweck dieses Design als Banner, Sticker oder als Schild an unseren Projekten anzubringen. Das Schild soll in zwei verschiedenen Layouts geliefert werden.
1. Eine Art Blanko Version in der das Logo und das Motto eingearbeitet sind. Dieser Teil nimmt rund 1/3 des Plakats ein. Der Rest hat einen Freiraum auf dem wir Namen der Spender oder kooperative Charity Logos einsetzen können. Diese Version wird für Zusammenarbeit verwendet.
2. Eine zweite Version nimmt das gesamte Plakat ein, hier findet sich das Logo und das Motto welche das ganze Plakat einnehmen.
In beiden Fällen sollte die Aufteilung sauber und gut leserlich sein. Das Plakat wird in Auflösungen von bis zu 1,5m mal 1m gedruckt, sollte dementsprechend also die richtige Auflösung haben. Außerdem sollten Photoshop Datei möglichst mitgeliefert werden damit wir wenn nötig Namen und Logos einsetzen können.
Das einzuarbeitende Motto lautet:
إنما المؤمنون أخوة
Das Plakat sollte im Querformat sein und die Hintergrundfarbe sollte schwarz oder weiß sein.
Anbei befindet sich eine Beispieldatei wie das Plakat an den Projekten angebracht wird.

```html
<!DOCTYPE html>
<html lang="de">
<head>
<meta charset="utf-8">
<title>Orvu – Plakat Kooperation</title>
<link rel="stylesheet" href="https://fonts.googleapis.com/css2?family=Harmattan:wght@400;600&display=swap">
<style>
  :root {
    --ink: #0e0e0c;
    --gold: #d3ae66;
    --blue: #1b76b8;
    --orange: #c9461f;
    --frame: #3a3a38;
  }
  html, body {
    margin: 0;
    padding: 0;
    overflow: hidden;
    background: var(--ink);
  }
  .poster {
    position: relative;
    width: 1200px;
    height: 848px;
    background: var(--ink);
    box-sizing: border-box;
    border: 1px solid var(--frame);
    overflow: hidden;
    font-family: "Harmattan", sans-serif;
  }
  .motto {
    position: absolute;
    left: 50px;
    top: 40px;
    width: 720px;
    margin: 0;
    direction: rtl;
    text-align: center;
    color: var(--gold);
    font-size: 118px;
    font-weight: 400;
    line-height: 1.2;
  }
  .band {
    position: absolute;
    left: 0;
    width: 100%;
  }
  .band--gold-top { top: 205px; height: 62px; background: var(--gold); }
  .band--blue-top { top: 276px; height: 8px; background: var(--blue); }
  .band--orange-top { top: 286px; height: 17px; background: var(--orange); }
  .band--orange-bottom { top: 750px; height: 17px; background: var(--orange); }
  .band--blue-bottom { top: 768px; height: 8px; background: var(--blue); }
  .band--gold-bottom { top: 785px; height: 63px; background: var(--gold); }
  .brand {
    position: absolute;
    left: 811px;
    top: 15px;
    width: 285px;
    height: 252px;
    background: var(--ink);
    display: flex;
    flex-direction: column;
    align-items: center;
    justify-content: center;
    gap: 22px;
  }
  .brand__mark {
    width: 96px;
    height: 96px;
    background: var(--gold);
  }
  .brand__name {
    color: var(--gold);
    font-size: 54px;
    font-weight: 600;
    letter-spacing: 4px;
    line-height: 1;
    text-transform: uppercase;
  }
  .donor-area {
    position: absolute;
    left: 0;
    top: 303px;
    width: 100%;
    height: 447px;
  }
</style>
</head>
<body>
  <div class="poster">
    <h1 class="motto" lang="ar">إنما المؤمنون أخوة</h1>

    <div class="band band--gold-top"></div>
    <div class="brand">
      <div class="brand__mark"></div>
      <div class="brand__name">Kastrel</div>
    </div>
    <div class="band band--blue-top"></div>
    <div class="band band--orange-top"></div>

    <div class="donor-area"></div>

    <div class="band band--orange-bottom"></div>
    <div class="band band--blue-bottom"></div>
    <div class="band band--gold-bottom"></div>
  </div>
</body>
</html>
```